Fairway Outback Links Saver Pass

We need a design for a plastic rewards card that we would like to offer to our customers. The rewards card is for customers to show other golf courses to indicate that they get a discount at that participating course. Our Company name is "Fairway Outback" the card is called the "Links Saver Pass" and our tag line is "Swing Often Spend Little". We would like the card to have an Australian feel and and use the colours Black and Yellow.

Target Market(s)

Golfers

Industry/Entity Type

Plastic

Requirements
Must have
• We have attached how our previous version looked with the detail that needs to be on the card. However the addresses on the front of the card needs to be removed and replaced with www.fairwayoutback.com.au. On the back of the card the address needs to be changed to "Fairway Outback" P.O Box 4182, Hidden Cove W.A. Email: info@fairwayoutback.com.au

```html
<!DOCTYPE html>
<html lang="en">
<head>
<meta charset="utf-8">
<title>Fairway Outback – Links Saver Pass</title>
<link rel="stylesheet" href="https://fonts.googleapis.com/css2?family=Arimo:wght@400;700&family=Noto+Sans:wght@400;700&display=swap">
<style>
  :root {
    --page: #ece8e1;
    --card: #262424;
    --yellow: #f2e600;
    --orange: #f0921e;
    --white: #ffffff;
    --grey-text: #c9c9c9;
    --field: #ececec;
    --band-light: #d8d8d8;
  }
  * { box-sizing: border-box; margin: 0; padding: 0; }
  html, body { width: 1200px; height: 509px; overflow: hidden; background: var(--page); }
  .canvas { position: relative; width: 1200px; height: 509px; }

  .card {
    position: absolute; top: 83px; width: 540px; height: 338px;
    background: var(--card); overflow: hidden;
    box-shadow: 0 3px 8px rgba(0,0,0,.35);
  }
  .card--front { left: 41px; font-family: "Arimo", Arial, sans-serif; }
  .card--back { left: 612px; font-family: "Noto Sans", Verdana, sans-serif; color: var(--white); }

  /* brand mark */
  .brand { position: absolute; display: flex; align-items: center; gap: 9px; }
  .brand__dot { width: 58px; height: 58px; border-radius: 50%; background: var(--orange); flex: none; }
  .brand__name { font-family: "Arimo", Arial, sans-serif; font-weight: 700; font-size: 17px; color: var(--white); white-space: nowrap; }
  .card--front .brand { left: 38px; top: 30px; }
  .card--back .brand { left: 330px; top: 248px; }

  /* front */
  .title-band { position: absolute; left: 278px; top: 23px; width: 262px; height: 59px; }
  .title-band__shade {
    position: absolute; left: 60px; right: 0; top: 29px; height: 30px;
    background: linear-gradient(90deg, rgba(216,216,216,0) 0%, rgba(150,150,150,.55) 45%, var(--band-light) 100%);
  }
  .title-band__name { position: absolute; right: 12px; top: 5px; font-size: 23px; color: var(--yellow); white-space: nowrap; }
  .title-band__product { position: absolute; right: 12px; top: 34px; font-size: 17px; color: #e6e6e6; white-space: nowrap; }

  .map-area {
    position: absolute; left: 18px; top: 96px; width: 252px; height: 214px;
    background:
      radial-gradient(ellipse 60% 55% at 62% 28%, rgba(150,150,150,.85) 0%, rgba(110,110,110,.6) 40%, rgba(38,36,36,0) 100%),
      radial-gradient(ellipse 70% 60% at 40% 60%, rgba(95,95,95,.7) 0%, rgba(38,36,36,0) 100%);
  }
  .ball-area {
    position: absolute; left: 366px; top: 94px; width: 144px; height: 144px; border-radius: 50%;
    background: radial-gradient(circle at 40% 25%, #9a9a9a 0%, #555 40%, #262424 80%);
  }
  .tagline {
    position: absolute; right: 22px; top: 252px;
    font-size: 22px; font-weight: 700; color: var(--yellow); white-space: nowrap;
  }
  .website {
    position: absolute; right: 23px; top: 291px;
    font-size: 16px; color: var(--grey-text); letter-spacing: 1.6px; white-space: nowrap;
  }

  /* back */
  .terms { position: absolute; left: 19px; top: 11px; width: 470px; }
  .label { color: var(--yellow); font-weight: 700; font-size: 13.5px; line-height: 16px; }
  .terms__list { list-style: none; font-size: 13.5px; line-height: 15.4px; }
  .terms__list li { position: relative; padding-left: 19px; }
  .terms__list li:last-child { white-space: nowrap; }
  .terms__list li::before {
    content: ""; position: absolute; left: 3px; top: 5px;
    width: 6px; height: 6px; border-radius: 50%; background: var(--yellow);
  }
  .field { position: absolute; top: 123px; }
  .field--name { left: 19px; }
  .field--expiry { left: 322px; }
  .field__box { margin-top: 3px; height: 57px; background: var(--field); border: 1px solid #bdbdbd; }
  .field--name .field__box { width: 287px; }
  .field--expiry .field__box { width: 198px; }
  .contact-note { position: absolute; left: 19px; top: 214px; font-size: 13.5px; line-height: 15.6px; }
  .address { position: absolute; left: 27px; top: 261px; font-size: 13.5px; line-height: 16.4px; font-style: normal; }
  .address .label { display: block; }
</style>
</head>
<body>
<div class="canvas">

  <section class="card card--front" aria-label="Card front">
    <div class="brand">
      <span class="brand__dot"></span>
      <span class="brand__name">Fairway Outback</span>
    </div>
    <div class="title-band">
      <div class="title-band__shade"></div>
      <div class="title-band__name">Fairway Outback</div>
      <div class="title-band__product">Links Saver Pass</div>
    </div>
    <div class="map-area" role="img" aria-label="Silver gradient map of Australia"></div>
    <div class="ball-area" role="img" aria-label="Dimpled grey golf ball illustration"></div>
    <div class="tagline">SWING OFTEN SPEND LITTLE!</div>
    <div class="website">www.fairwayoutback.com.au</div>
  </section>

  <section class="card card--back" aria-label="Card back">
    <div class="terms">
      <div class="label">Terms and Conditions</div>
      <ul class="terms__list">
        <li>Cardholders must show their card to redeem offers at the participating outlets</li>
        <li>The Discounts apply to the card holder only.</li>
        <li>Golf course bookings are essential.</li>
        <li>The discounts available on the card are not valid with any other offer.</li>
      </ul>
    </div>
    <div class="field field--name">
      <div class="label">Card Holder Name</div>
      <div class="field__box"></div>
    </div>
    <div class="field field--expiry">
      <div class="label">Expiry date</div>
      <div class="field__box"></div>
    </div>
    <p class="contact-note">For information regarding this card contact:<br>The Administration Coordinator</p>
    <address class="address">
      <span class="label">Fairway Outback</span>
      P.O Box 4182, Hidden Cove W.A.<br>
      Email: info@fairwayoutback.com.au
    </address>
    <div class="brand">
      <span class="brand__dot"></span>
      <span class="brand__name">Fairway Outback</span>
    </div>
  </section>

</div>
</body>
</html>
```